Smack you in the face - Landing page for Residential Electrical Repairs (Searchly Ads)

I need an effective landing page for Searchly ads. The ads will target residential electrical repairs. Lighting Outages, Power Outages, Breakers Tripping, Outlets Not Working. I need a strong call to action to Call Us Now! Forms don't work well for us so we only need one form as a last option at the bottom of the page. We only work on homes. the website is https://www.vantor-wiring.example/
email is : support@vantor-wiring.example
Phone 555-217-4086

**This is about one focused service. Electrical Repairs - That includes Partial Power Outages, Outlets Not Working, Tripped Breakers, Electrical Panel repairs, and Fusebox Repairs. The area served will only be Greenville, SC. KOBA is the platform

Target Market(s)

Homeonwers in need of electrical repair

Industry/Entity Type

Residential Electricians

Coding

Coded - Design and coding required

Requirements
Must have
• Strong to action for phone calls, this landing page must grab action fast.
Nice to have
• Social proof with existing 5 start reviews for Searchly, Rately, TCB, and Friendnet
Should not have
• Should not be form based. I do not like the site's current them, please don't copy it. Make your own.

```html
<!DOCTYPE html>
<html lang="en">
<head>
<meta charset="utf-8">
<title>Vantor Wiring Service – Electrical Repairs in Greenville, SC</title>
<link href="https://fonts.googleapis.com/css2?family=Krona+One&family=Oswald:wght@500;600&family=Poppins:wght@400;500;600&display=swap" rel="stylesheet">
<style>
:root{
  --orange:#f26a21;
  --teal:#1e6781;
  --teal-dark:#174f63;
  --ink:#1b1b1b;
  --muted:#5a5a5a;
  --white:#fff;
}
*{box-sizing:border-box;margin:0;padding:0}
html,body{width:1200px;height:4874px;overflow:hidden}
body{position:relative;font-family:"Poppins",sans-serif;color:var(--ink);background:var(--white)}
.abs{position:absolute}
.heading{font-family:"Krona One",sans-serif;text-transform:uppercase;letter-spacing:1px}
.eyebrow{font-size:12px;text-transform:uppercase;letter-spacing:.3px}
.rule{height:3px;width:48px;background:var(--orange)}
.center{left:0;width:1200px;text-align:center}
.btn{display:flex;align-items:center;justify-content:center;font-size:12px;font-weight:600;text-transform:uppercase;color:#fff;background:var(--orange);border-radius:3px;white-space:nowrap}
.bolt-btn{display:flex;align-items:center}
.bolt-btn svg{width:32px;height:46px;margin-right:-6px;z-index:1}
.bolt-btn span{height:36px;display:flex;align-items:center;justify-content:center;padding:0 10px;font-size:11px;font-weight:500;text-transform:uppercase;white-space:nowrap}
.bolt-btn.solid span{background:var(--orange);color:#fff}
.bolt-btn.light span{background:#fff;color:var(--orange)}
/* hero */
.hero-photo{left:0;top:0}
.logo{display:flex;align-items:center;gap:10px}
.logo-dot{width:16px;height:16px;border-radius:50%;background:var(--orange)}
.logo-name{font-family:"Poppins",sans-serif;font-weight:600;font-size:20px;color:#fff;line-height:1}
.hero-title{left:142px;top:222px;font-family:"Oswald",sans-serif;font-weight:500;color:#fff;font-size:40px;line-height:49px}
.hero-sub{left:142px;top:327px;width:510px;font-family:"Oswald",sans-serif;font-size:16px;line-height:28px;color:#fff}
.badge{left:795px;top:436px;width:284px;height:284px;border-radius:50%;border:8px solid #2a8bb0;background:linear-gradient(160deg,#3a5f8c,#1f3f6a);color:#fff;text-align:center}
.badge b{display:block;margin-top:76px;font-size:56px;font-family:"Poppins",sans-serif;font-weight:600;line-height:1}
.badge p{font-size:21px;font-weight:500;line-height:27px;margin-top:8px}
/* services */
.services{left:0;top:767px;width:1200px;height:788px;background:var(--teal)}
.card{position:absolute;top:188px;width:215px;height:444px;background:#fff;border-radius:10px;overflow:hidden;text-align:center}
.card .ph{height:255px}
.card h3{margin-top:38px;font-size:13px;font-weight:600;text-transform:uppercase}
.card p{margin:10px 14px 0;font-size:10px;line-height:19px;color:var(--muted)}
.card a{display:block;margin-top:10px;font-size:10px;color:var(--orange);text-decoration:underline;text-transform:uppercase}
/* reviews */
.reviews{left:0;top:1900px;width:1200px;height:558px;background:var(--orange);color:#fff}
.platforms{top:185px;left:0;width:1200px;display:flex;justify-content:center;gap:26px;font-weight:600;font-size:16px}
.platforms div{text-align:center;line-height:16px}
.platforms small{display:block;font-size:10px;letter-spacing:1px}
.review{position:absolute;top:280px;height:190px;background:#fff;color:var(--ink);text-align:center;border-bottom:4px solid #e9e9e9}
.review .av{position:absolute;top:-36px;left:50%;margin-left:-34px;width:68px;height:68px;border-radius:50%;border:3px solid #fff;background:#c9a48c}
.review h4{margin-top:46px;font-size:14px;font-weight:600}
.review .stars{color:var(--orange);font-size:11px;letter-spacing:1px}
.review p{margin:8px 22px 0;font-size:10px;line-height:19px;color:#444}
.arrow{position:absolute;top:360px;width:34px;height:34px;border-radius:50%;border:1px solid #fff;display:flex;align-items:center;justify-content:center}
/* gallery */
.tile{position:absolute;border-radius:4px}
/* why */
.why-item{position:absolute;top:3770px;width:260px;text-align:center;font-size:15px;line-height:27px}
.why-item svg{display:block;margin:0 auto 40px}
/* contact */
.contact{left:0;top:4090px;width:1200px;height:475px;background:linear-gradient(180deg,#3b3f45,#24282c);color:#fff}
.c-item{position:absolute;left:142px;display:flex;align-items:center;gap:22px;font-size:14px;line-height:20px}
.c-icon{width:48px;height:48px;border-radius:50%;border:1px solid #fff;display:flex;align-items:center;justify-content:center}
.form{position:absolute;left:653px;top:40px;width:405px;height:370px;background:rgba(255,255,255,.93)}
.field{position:absolute;height:30px;background:#e8e8e8;font-size:10px;color:#555;padding:8px 10px}
.submit{position:absolute;left:0;bottom:0;width:405px;height:60px;background:var(--orange);color:#fff;font-weight:600;font-size:14px;display:flex;align-items:center;justify-content:center}
/* footer */
.copyright{left:0;top:4848px;width:1200px;height:26px;background:var(--teal);color:#fff;font-size:11px;display:flex;align-items:center;justify-content:center}
.social{width:34px;height:34px;border-radius:50%;background:var(--orange)}
</style>
</head>
<body>
<svg class="abs" width="0" height="0"><defs>
<symbol id="bolt" viewBox="0 0 32 46"><polygon points="18,0 2,26 13,26 6,46 30,16 18,16 26,0" fill="#f26a21"/></symbol>
</defs></svg>

<!-- hero -->
<svg class="abs hero-photo" width="1200" height="770" role="img" aria-label="Aerial view of downtown Greenville skyline with trees">
  <defs><linearGradient id="sky" x1="0" y1="0" x2="0" y2="1">
    <stop offset="0" stop-color="#4f7aa8"/><stop offset=".45" stop-color="#6b7e84"/><stop offset="1" stop-color="#3f5a3a"/></linearGradient></defs>
  <path d="M0,0H1200V400C1050,615 800,722 520,720C300,718 120,680 0,640Z" fill="url(#sky)"/>
  <path d="M1200,400C1050,615 800,722 520,720C300,718 120,680 0,640V660C120,700 300,740 520,742C820,745 1070,640 1200,440Z" fill="#f26a21"/>
</svg>
<div class="abs logo" style="left:142px;top:36px"><span class="logo-dot"></span><span class="logo-name">VANTOR WIRING</span></div>
<div class="abs btn" style="left:727px;top:32px;width:133px;height:36px">Call Us Now!</div>
<div class="abs" style="left:876px;top:30px;width:40px;height:40px;border-radius:50%;background:#fff;display:flex;align-items:center;justify-content:center">
  <svg width="18" height="18" viewBox="0 0 24 24"><path d="M6.6 10.8a15 15 0 006.6 6.6l2.2-2.2a1 1 0 011-.25 11.4 11.4 0 003.6.57 1 1 0 011 1V20a1 1 0 01-1 1A17 17 0 013 4a1 1 0 011-1h3.5a1 1 0 011 1c0 1.25.2 2.45.57 3.57a1 1 0 01-.25 1z" fill="#1e6781"/></svg>
</div>
<div class="abs" style="left:930px;top:28px;color:#fff;font-size:16px;line-height:21px">Phone<br>555-217-4086</div>
<h1 class="abs hero-title">Make Us Your First Choice For<br>Electrical Services</h1>
<p class="abs hero-sub">Licensed Electricians In Greenville, SC Ensuring Top-tier Service For Every Call.</p>
<div class="abs btn" style="left:142px;top:392px;width:126px;height:34px">Call Us Now!</div>
<div class="abs badge" role="img" aria-label="Two electricians in blue uniforms giving thumbs up">
  <b>8+</b><p>Years Of<br>Experience</p>
</div>

<!-- services -->
<section class="abs services">
  <p class="abs eyebrow center" style="top:84px;color:#fff">Our Services</p>
  <h2 class="abs heading center" style="top:104px;font-size:30px;color:#fff">What We Do</h2>
  <div class="abs rule" style="left:576px;top:152px;background:#fff"></div>
  <div class="card" style="left:142px"><div class="ph" role="img" aria-label="Hand testing a circuit breaker" style="background:linear-gradient(160deg,#8a8f95,#3b3f44)"></div><h3>Partial Power Outages</h3><p>Prolonged darkness or interrupted power supply can disrupt your routine. We ensure that your power is restored swiftly.</p><a>Learn More</a></div>
  <div class="card" style="left:376px"><div class="ph" role="img" aria-label="Multimeter testing a wall outlet" style="background:linear-gradient(160deg,#d7d7d4,#9a958c)"></div><h3>Outlets Not Working</h3><p>As foundational elements of any residential or commercial property, outlets and switches are easy to overlook—until they stop...</p><a>Learn More</a></div>
  <div class="card" style="left:611px"><div class="ph" role="img" aria-label="Electrician working on an electrical panel" style="background:linear-gradient(160deg,#c4c7ca,#5a5d61)"></div><h3>Electrical Panel Repairs</h3><p>From minor glitches to significant malfunctions, we're adept at diagnos &amp; resolving all electrical panel issues.</p><a>Learn More</a></div>
  <div class="card" style="left:843px"><div class="ph" role="img" aria-label="Electrician in hard hat inspecting a fuse box" style="background:linear-gradient(160deg,#b9bec4,#3d4651)"></div><h3>Fusebox Repairs</h3><p>Protect your electrical system with our expert fuse box repair services. Lorem ipsum dolor sit consectetur adipiscing elit.</p><a>Learn More</a></div>
  <div class="abs bolt-btn light" style="left:508px;top:660px"><svg><use href="#bolt"/></svg><span style="width:178px">Call Us Now!</span></div>
</section>

<!-- tagline -->
<h2 class="abs heading center" style="top:1632px;font-size:30px;line-height:43px;color:var(--teal)">Try Our Services Once And You<br>Won’t Need To Go Anywhere Else</h2>
<p class="abs center" style="top:1722px;font-size:17px">Expert Solutions And Excellent Service</p>
<div class="abs bolt-btn solid" style="left:508px;top:1766px"><svg><use href="#bolt"/></svg><span style="width:178px">Call Us Now!</span></div>

<!-- reviews -->
<section class="abs reviews">
  <p class="abs eyebrow center" style="top:82px">Testimonials</p>
  <h2 class="abs heading center" style="top:100px;font-size:32px;color:#111">Customer Reviews</h2>
  <div class="abs rule" style="left:576px;top:150px;background:#111"></div>
  <div class="abs platforms">
    <div>Searchly<small>★★★★★</small></div>
    <div>Rately<small>★★★★★</small></div>
    <div style="display:flex;align-items:center;gap:6px"><span style="width:22px;height:28px;background:#fff;display:inline-block"></span>TCB</div>
    <div>Friendnet<small>★★★★★</small></div>
  </div>
  <div class="arrow" style="left:85px"><svg width="10" height="14"><path d="M8 1L2 7l6 6" stroke="#fff" fill="none" stroke-width="1.5"/></svg></div>
  <div class="review" style="left:142px;width:423px">
    <div class="av" role="img" aria-label="Reviewer portrait"></div>
    <h4>Dana Whitfield</h4><div class="stars">★★★★★</div>
    <p>Searched to find an electrician and MILO from Vantor Wiring responded. He was very friendly, professional and showed interest in my dilemma. He made it easy to talk to and help me understand the urgency of my situation. He not only solved the issue...</p>
  </div>
  <div class="review" style="left:617px;width:441px">
    <div class="av" role="img" aria-label="Reviewer portrait" style="background:#b98a6c"></div>
    <h4>Karina Solberg</h4><div class="stars">★★★★★</div>
    <p>Milo was wonderful and immediately identified what was tripping an electrical breaker box out by our pool. He then installed an electrical outlet for me that I requested in the attic; both jobs done very well in about an hours time. Thank you Milo! Will definitely...</p>
  </div>
  <div class="arrow" style="left:1082px;border:none"><svg width="10" height="14"><path d="M2 1l6 6-6 6" stroke="#fff" fill="none" stroke-width="1.5"/></svg></div>
</section>

<!-- gallery -->
<p class="abs eyebrow center" style="top:2541px;color:var(--orange)">Our Projects</p>
<h2 class="abs heading center" style="top:2562px;font-size:30px">Work Gallery</h2>
<div class="abs rule" style="left:576px;top:2610px"></div>
<div class="tile" style="left:142px;top:2645px;width:276px;height:403px;background:linear-gradient(180deg,#4a4f4c,#2c2f30);color:#fff;text-align:center" role="img" aria-label="Electrician working at an outdoor meter box">
  <p style="margin-top:138px;font-weight:600;font-size:14px">LOREM IPSUM DOLOR</p>
  <p style="margin:8px 30px 0;font-size:10px;line-height:19px;opacity:.85">Lorem ipsum dolor sit amet, consectetur adipiscing elit. Vestibulum laoreet ex ac interdum sodales.</p>
  <div style="margin:12px auto 0;width:34px;height:34px;border-radius:50%;border:1px solid #fff;font-size:22px;line-height:30px">+</div>
</div>
<div class="tile" style="left:432px;top:2645px;width:336px;height:195px;background:linear-gradient(160deg,#d2d4d6,#7f868c)" role="img" aria-label="Hand adjusting breakers in a panel"></div>
<div class="tile" style="left:432px;top:2852px;width:336px;height:196px;background:linear-gradient(160deg,#e7e2dc,#b79a80)" role="img" aria-label="Hands wiring a wall socket"></div>
<div class="tile" style="left:782px;top:2645px;width:276px;height:403px;background:linear-gradient(160deg,#7a7f84,#2e3236)" role="img" aria-label="Hand testing breaker with a tester"></div>

<!-- call band -->
<div class="abs" style="left:0;top:3243px;width:1200px;height:274px;background:var(--teal)"></div>
<div class="abs" style="left:170px;top:3120px;width:260px;height:397px;background:linear-gradient(180deg,#e88a3a,#2f5fb0);border-radius:120px 120px 0 0" role="img" aria-label="Smiling electrician in orange hard hat and blue overalls giving thumbs up"></div>
<h2 class="abs heading" style="left:510px;top:3306px;font-size:32px;color:#fff">Need Our Services?</h2>
<p class="abs" style="left:494px;top:3354px;font-size:16px;color:#fff">Vantor Wiring Service Can Be Contacted In a Number of Ways</p>
<div class="abs bolt-btn solid" style="left:600px;top:3396px"><svg><use href="#bolt"/></svg><span style="width:132px">Call Us Now!</span></div>
<div class="abs bolt-btn solid" style="left:773px;top:3396px"><svg><use href="#bolt"/></svg><span style="width:154px">555-217-4086</span></div>

<!-- why choose us -->
<p class="abs eyebrow center" style="top:3598px;color:var(--orange)">Benefits</p>
<h2 class="abs heading center" style="top:3620px;font-size:30px">Why Choose Us</h2>
<div class="abs rule" style="left:576px;top:3668px"></div>
<p class="abs center" style="top:3696px;font-size:13px;line-height:26px">Need to hire a local electrician? Vantor Wiring Service is the company to call.<br>You'll be pleased to know that</p>
<div class="why-item" style="left:180px">
  <svg width="70" height="70" viewBox="0 0 70 70"><circle cx="40" cy="30" r="28" fill="#f1f1f1"/><circle cx="32" cy="38" r="6" fill="none" stroke="#333" stroke-width="2"/><path d="M22 58c0-8 20-8 20 0z" fill="none" stroke="#333" stroke-width="2"/><text x="14" y="22" font-size="12" fill="#f26a21">★ ★ ★</text></svg>
  We Have A Decade<br>of Experience</div>
<div class="why-item" style="left:452px">
  <svg width="70" height="70" viewBox="0 0 70 70"><circle cx="40" cy="30" r="28" fill="#f1f1f1"/><rect x="22" y="10" width="26" height="34" fill="none" stroke="#333" stroke-width="2"/><path d="M27 18h16M27 24h16M27 30h10" stroke="#333"/><circle cx="34" cy="48" r="7" fill="none" stroke="#f26a21" stroke-width="2"/></svg>
  Vantor Wiring Service Is<br>Fully Licensed And Insured</div>
<div class="why-item" style="left:743px">
  <svg width="70" height="70" viewBox="0 0 70 70"><circle cx="40" cy="30" r="28" fill="#f1f1f1"/><rect x="20" y="14" width="18" height="38" fill="none" stroke="#333" stroke-width="2"/><rect x="34" y="24" width="20" height="26" fill="none" stroke="#333" stroke-width="2"/><path d="M38 30h12M38 36h4M44 36h4M38 42h4M44 42h4" stroke="#f26a21" stroke-width="2"/></svg>
  We Offer Free Estimates</div>
<div class="abs bolt-btn solid" style="left:508px;top:3960px"><svg><use href="#bolt"/></svg><span style="width:178px">Call Us Now!</span></div>

<!-- contact -->
<section class="abs contact" role="img" aria-label="Dimmed city skyline backdrop">
  <p class="abs eyebrow" style="left:142px;top:100px">Quick Contact</p>
  <h2 class="abs heading" style="left:142px;top:118px;font-size:32px;color:#fff">Get In Touch</h2>
  <div class="abs rule" style="left:142px;top:166px;background:#fff"></div>
  <div class="c-item" style="top:188px"><span class="c-icon"><svg width="16" height="22" viewBox="0 0 16 22"><path d="M8 1a7 7 0 00-7 7c0 5 7 13 7 13s7-8 7-13a7 7 0 00-7-7z" fill="none" stroke="#fff" stroke-width="1.8"/><circle cx="8" cy="8" r="2.5" fill="#fff"/></svg></span><span>412 Larkspur Ave Suite 9<br>Greenville, SC 29601</span></div>
  <div class="c-item" style="top:262px"><span class="c-icon"><svg width="18" height="18" viewBox="0 0 24 24"><path d="M6.6 10.8a15 15 0 006.6 6.6l2.2-2.2a1 1 0 011-.25 11.4 11.4 0 003.6.57 1 1 0 011 1V20a1 1 0 01-1 1A17 17 0 013 4a1 1 0 011-1h3.5a1 1 0 011 1c0 1.25.2 2.45.57 3.57a1 1 0 01-.25 1z" fill="#fff"/></svg></span><span><b style="font-weight:600">Call Us Now!</b><br>555-217-4086</span></div>
  <div class="c-item" style="top:336px"><span class="c-icon"><svg width="20" height="14" viewBox="0 0 20 14"><rect x="1" y="1" width="18" height="12" fill="none" stroke="#fff" stroke-width="1.6"/><path d="M1 1l9 7 9-7" fill="none" stroke="#fff" stroke-width="1.6"/></svg></span><span><b style="font-weight:600">Email</b><br>support@vantor-wiring.example</span></div>
  <div class="form">
    <div class="field" style="left:40px;top:45px;width:160px">First Name</div>
    <div class="field" style="left:210px;top:45px;width:160px">Last Name</div>
    <div class="field" style="left:40px;top:95px;width:160px">Email Address</div>
    <div class="field" style="left:210px;top:95px;width:160px">Phone Number</div>
    <div class="field" style="left:40px;top:145px;width:330px;height:115px;padding-top:16px">Write Comments</div>
    <div class="submit">Submit Now</div>
  </div>
</section>

<!-- footer -->
<div class="abs" style="left:0;top:4625px;width:1200px;display:flex;justify-content:center;align-items:center;gap:14px">
  <span style="width:24px;height:24px;border-radius:50%;background:var(--orange)"></span>
  <span style="font-weight:600;font-size:36px;color:var(--teal);letter-spacing:2px">VANTOR WIRING</span>
</div>
<div class="abs" style="left:0;top:4696px;width:1200px;text-align:center;font-size:15px;font-weight:600;letter-spacing:5px;color:var(--teal)">ELECTRICAL SERVICE</div>
<div class="abs" style="left:0;top:4753px;width:1200px;display:flex;justify-content:center;gap:16px">
  <span class="social" aria-label="Friendnet"></span><span class="social" aria-label="Social profile"></span><span class="social" aria-label="Professional network"></span>
</div>
<div class="abs copyright">Copyright © 2023 VANTOR WIRING SERVICE. All Rights Reserved.</div>
</body>
</html>
```